National Rent-to-Own sheds company needs new coded front end web page

Kestrel Lease provides a rent-to-own financing option to storage building dealers in the southeast U.S. We need a redesign of Kestrel Lease's front end web site.

Current site is https://www.kestrellease.example/

I'm looking to get a coded (HTML & CSS) single page design. I am a PHP developer and looking to outsource the design of the front end of the site. You don't have to make anything work beyond HTML and CSS. I would like the layout to be done in Bootstrap and as such the CSS would already be done. You would just have to add your supplemental CSS for whatever background, colors, fonts, or custom elements that need to be styled.

The client's website does not have a whole lot of content, as you can see if you visit the page, so I'd like to turn the current front-end with multiple pages into a single page. Most of the content is quite short and I'd like an artful way to present it. I'd like to actually remove the menu at the top.

See this site for examples of Bootstrap layouts: https://layoutbazaar.example/themes/business?branch=3.x

If all goes well with this project, we would like to continue to work with the designer in the near future on some other similar projects.
Updates

I have updated the brief for single page design clarification.

The About Us page is a duplicate of the home page, so you can ignore that. The Rental Programs offered are actually 24, 36, 48, and 60. The FAQs page we will probably link to a modal window, so don't worry about its content; we just need a way to provide the link to it. The contact page info could use some nice styling. The Dealer Login page should become a single button like the Customer Payments at the top.

Industry/Entity Type

Building

Font styles to use
Sans Serif

Colors

Designer to choose colors to be used in the design.

Requirements
Must have
• The new design should be marked up with Bootstrap 3. It should be a responsive layout. The HTML, CSS, and any image assets should be provided. A PSD or other design file is not required, but we'll certainly take it if you made one anyway.

Clean, simple design.
Nice to have
• Some stock photography may help to explain in a glance what Kestrel Lease does. Some keywords to look for in stock photos: storage buildings, storage sheds, backyard storage, rent-to-own, barns. Note that you don't need to purchase the stock photos. Just use watermarked placeholders in your layout.

```html
<!DOCTYPE html>
<html lang="en">
<head>
<meta charset="utf-8">
<title>Kestrel Lease — Rent to Own Storage Buildings</title>
<link rel="stylesheet" href="https://fonts.googleapis.com/css2?family=Open+Sans:wght@400;600;700&family=Roboto+Condensed:wght@400;700&family=Roboto:wght@400;500;700&display=swap">
<style>
:root{
  --navy:#0d2c5a;
  --orange:#f47a20;
  --blue-band:#0c4166;
  --blue-band-dark:#08314f;
  --ink:#222;
  --muted:#555;
  --faq-bg:#f3f3f3;
  --contact-bg:#333333;
  --footer-bg:#1d1d1d;
  --line-dark:#4a4a4a;
}
*{box-sizing:border-box;margin:0;padding:0}
html,body{width:1200px;height:3485px;overflow:hidden}
body{font-family:"Open Sans",Arial,sans-serif;color:var(--ink);background:#fff;position:relative}

/* Header */
.site-header{height:72px;background:#fff;position:relative;box-shadow:0 1px 3px rgba(0,0,0,.15);z-index:2}
.brand{position:absolute;left:150px;top:18px;display:flex;align-items:center;gap:8px;font-family:"Roboto",sans-serif;font-weight:700;font-size:24px;color:var(--navy)}
.brand-dot{width:14px;height:14px;background:var(--orange);border-radius:50%}
.main-nav{position:absolute;left:350px;top:0;height:72px;display:flex}
.main-nav a{display:flex;align-items:center;padding:0 18px;height:72px;font-family:"Roboto",sans-serif;font-size:13px;color:#888;text-decoration:none;background:#f6f6f6;border-right:1px solid #e6e6e6}
.main-nav a.active{background:#fff;color:#333}
.main-nav a.btn-dealer{background:var(--orange);color:#fff;font-weight:700;margin-left:6px;border:0}
.main-nav a.btn-payments{background:var(--navy);color:#fff;font-weight:700;margin-left:6px;border:0}

/* Hero */
.hero{position:absolute;top:72px;left:0;width:1200px;height:508px;
  background:linear-gradient(180deg,#9cc3e2 0%,#c9dcea 35%,#d4b07a 55%,#b8884c 80%,#6d7a48 100%)}
.hero-title{position:absolute;left:0;right:0;top:232px;text-align:center;font-family:"Roboto",sans-serif;font-weight:700;font-size:36px;line-height:1.15}
.hero-title span{display:inline-block;color:#fff;padding:2px 10px}
.hero-title .line-navy{background:var(--navy)}
.hero-title .line-orange{background:var(--orange)}

/* Shared section heading */
.section-title{font-family:"Roboto Condensed",sans-serif;font-weight:700;font-size:26px;text-align:center;letter-spacing:.2px}
.section-title::after{content:"";display:block;width:88px;height:3px;background:var(--navy);margin:14px auto 0}
.body-copy{width:600px;margin:0 auto;text-align:center;font-size:12px;line-height:20px;color:var(--muted)}
.body-copy p+p{margin-top:20px}

/* Welcome / About */
.welcome{position:absolute;top:645px;left:0;width:1200px}
.welcome .section-title{color:var(--navy)}
.welcome .body-copy{margin-top:42px}
.divider{position:absolute;top:998px;left:240px;width:720px;height:1px;background:#ddd}
.divider-photo{position:absolute;top:940px;left:542px;width:116px;height:116px;border-radius:50%;border:4px solid #fff;box-shadow:0 0 0 1px #ddd;
  background:linear-gradient(180deg,#9fb9cf 0%,#8a4a35 45%,#6b7f4a 100%)}
.about{position:absolute;top:1123px;left:0;width:1200px}
.about .section-title{color:var(--navy)}
.about .body-copy{margin-top:50px}

/* Rental options */
.rental{position:absolute;top:1430px;left:0;width:1200px;height:525px;color:#fff;text-align:center;
  background:linear-gradient(135deg,var(--blue-band) 0%,var(--blue-band-dark) 50%,var(--blue-band) 100%)}
.rental .section-title{margin-top:57px;color:#fff}
.rental .section-title::after{background:#fff}
.rental-sub{font-family:"Roboto",sans-serif;font-size:24px;margin-top:42px}
.terms{position:relative;width:620px;height:140px;margin:32px auto 0}
.terms-line{position:absolute;left:60px;right:60px;top:55px;height:1px;background:rgba(255,255,255,.5)}
.term{position:absolute;top:0;width:110px;text-align:center}
.term-circle{width:110px;height:110px;border-radius:50%;border:4px solid #fff;background:var(--blue-band-dark);display:flex;align-items:center;justify-content:center;font-family:"Roboto",sans-serif;font-size:38px}
.term-label{font-family:"Roboto",sans-serif;font-size:15px;margin-top:10px}
.rental .body-copy{color:#fff;margin-top:20px;width:640px}

/* FAQ */
.faq{position:absolute;top:1955px;left:0;width:1200px;height:450px;background:var(--faq-bg);text-align:center}
.faq .section-title{margin-top:58px;color:var(--orange)}
.faq .section-title::after{width:310px;background:var(--orange);margin-top:18px}
.faq-sub{font-family:"Roboto",sans-serif;font-size:24px;color:var(--navy);margin-top:26px}
.faq-item{margin-top:28px}
.faq-q{font-family:"Roboto",sans-serif;font-weight:700;font-size:15px;color:var(--ink)}
.faq-a{width:500px;margin:6px auto 0;font-size:11.5px;line-height:19px;color:var(--muted)}

/* Contact */
.contact{position:absolute;top:2405px;left:0;width:1200px;height:978px;background:var(--contact-bg);color:#ddd;font-family:"Roboto",sans-serif}
.contact .section-title{margin-top:60px;color:#fff}
.contact .section-title::after{background:#fff}
.contact-col{position:absolute;top:188px;width:420px;text-align:center}
.contact-col.left{left:160px}
.contact-col.right{left:620px}
.dept{font-size:19px;color:#fff}
.dept-phone{font-size:27px;color:#fff;font-weight:500;line-height:30px}
.person{font-size:13px;line-height:22px;color:#bbb;white-space:nowrap}
.person b{color:#fff;font-weight:700}
.group{border-top:1px solid var(--line-dark);width:300px;margin:0 auto;padding:10px 0}
.group.first{border-top:0;margin-top:12px}
.group-head{font-weight:700;color:#fff;font-size:14px}
.legal{margin-top:14px}
.contact-address{position:absolute;top:780px;left:300px;width:600px;border-top:1px solid var(--line-dark);text-align:center;padding-top:40px;font-size:13px;line-height:24px;color:#aaa;font-style:normal}
.contact-address b{color:#fff}

/* Footer */
.site-footer{position:absolute;top:3383px;left:0;width:1200px;height:102px;background:var(--footer-bg);color:#999;font-size:12px;font-family:"Roboto",sans-serif}
.footer-numbers{position:absolute;top:18px;left:0;width:1200px;display:flex;justify-content:center;gap:28px}
.footer-numbers b{color:#fff;font-weight:400}
.footer-numbers .sep{color:#fff}
.footer-address{position:absolute;left:150px;top:52px;font-size:11px;line-height:18px;color:#777}
.footer-legal{position:absolute;right:150px;top:52px;font-size:11px;line-height:18px;color:#777;text-align:right}
</style>
</head>
<body>

<header class="site-header">
  <div class="brand"><span class="brand-dot"></span>Kestrel Lease</div>
  <nav class="main-nav">
    <a href="#" class="active">Home</a>
    <a href="#about">About Us</a>
    <a href="#rental">Rental Programs</a>
    <a href="#faq">FAQ</a>
    <a href="#contact">Contact Us</a>
    <a href="#" class="btn-dealer">Dealer Login</a>
    <a href="#" class="btn-payments">Customer Payments</a>
  </nav>
</header>

<section class="hero" role="img" aria-label="Photo of a timber-framed storage barn under construction against a blue sky">
  <h1 class="hero-title">
    <span class="line-navy">Why pay offsite storage</span><br>
    <span class="line-orange">when you can rent to own</span>
  </h1>
</section>

<section class="welcome">
  <h2 class="section-title">WELCOME TO KESTREL LEASE</h2>
  <div class="body-copy">
    <p>Kestrel Lease provides affordable alternatives for your storage needs. Unlike off-site self-storage, Kestrel Lease provides a path to ownership. As an industry leader, we partner with proven, successful storage building retailers and manufacturers to provide quality storage - in your backyard.</p>
    <p>We are pioneers in providing flexible payment options so you can match a rental plan to fit your storage building needs. Ask your retailer about our 24, 36, 48, and 60-month payment options. Why rent self-storage when you can rent then own!</p>
  </div>
</section>

<div class="divider"></div>
<div class="divider-photo" role="img" aria-label="Round photo of a red-roofed wooden storage shed"></div>

<section class="about" id="about">
  <h2 class="section-title">ABOUT US</h2>
  <div class="body-copy">
    <p>Kestrel Lease provides affordable alternatives for your storage needs. Unlike off-site self-storage, Kestrel Lease provides a path to ownership. As an industry leader, we partner with proven, successful storage building retailers and manufacturers to provide quality storage - in your backyard.</p>
    <p>We are pioneers in providing flexible payment options so you can match a rental plan to fit your storage building needs. Ask your retailer about our 24, 36, 48, and 60-month payment options. Why rent self-storage when you can rent then own!</p>
  </div>
</section>

<section class="rental" id="rental">
  <h2 class="section-title">RENTAL OPTIONS</h2>
  <div class="rental-sub">4 Rental Terms</div>
  <div class="terms">
    <div class="terms-line"></div>
    <div class="term" style="left:0"><div class="term-circle">24</div><div class="term-label">Months</div></div>
    <div class="term" style="left:155px"><div class="term-circle">36</div><div class="term-label">Months</div></div>
    <div class="term" style="left:310px"><div class="term-circle">48</div><div class="term-label">Months</div></div>
    <div class="term" style="left:465px"><div class="term-circle">60</div><div class="term-label">Months</div></div>
  </div>
  <div class="body-copy">
    <p>Match the rental plan with the storage building that fits your needs. As a leader in providing creative, affordable storage solutions, Kestrel Lease provides plans that are best suited for you. All Rental Purchase Agreements allow for early payoffs with no penalties. Why rent self-storage? Rent then Own!</p>
  </div>
</section>

<section class="faq" id="faq">
  <h2 class="section-title">FREQUENTLY ASKED QUESTIONS</h2>
  <div class="faq-sub">Common Questions</div>
  <div class="faq-item">
    <div class="faq-q">Do you require a deposit?</div>
    <p class="faq-a">Kestrel Lease requires your first and last month's payment prior to delivery of your building. Your last month payment is held in deposit and applied to your last payment in your contract or payoff amount.</p>
  </div>
  <div class="faq-item">
    <div class="faq-q">When do my payments begin?</div>
    <p class="faq-a">Your first payment will be due on the 5th of the month following the delivery of the building. The delivery person will provide you with the first payment coupon and you will receive a payment coupon book in the mail to use for all future payments.</p>
  </div>
</section>

<section class="contact" id="contact">
  <h2 class="section-title">CONTACT US</h2>

  <div class="contact-col left">
    <div class="dept">Common Questions</div>
    <div class="dept-phone">800-555-0142</div>
    <div class="group first">
      <div class="person"><b>Holly</b> – holly@kestrellease.example ext 2</div>
      <div class="person"><b>Dana</b> – dana@kestrellease.example ext 1</div>
    </div>
    <div class="group">
      <div class="group-head">Kirk Hollins</div>
      <div class="person">kirk@kestrellease.example</div>
      <div class="person">SC, NC, VA and Eastern TN</div>
    </div>
    <div class="group">
      <div class="group-head">Kent Rowland</div>
      <div class="person">kent@kestrellease.example</div>
      <div class="person">GA, FL, AL</div>
    </div>
    <div class="group">
      <div class="group-head">Bart Dunmore</div>
      <div class="person">bart@kestrellease.example</div>
      <div class="person">MS, LA, AR, Western TN</div>
    </div>
    <div class="group">
      <div class="group-head">Owen Jarvis</div>
      <div class="person">owen@kestrellease.example</div>
      <div class="person">TX, OK</div>
    </div>
  </div>

  <div class="contact-col right">
    <div class="dept">Payment Center</div>
    <div class="dept-phone">800-555-0177</div>
    <div class="group first"><div class="group-head">Account Managers</div></div>
    <div class="group"><div class="person"><b>Mandy</b> – mandy@kestrellease.example ext 1</div></div>
    <div class="group"><div class="person"><b>Lena</b> – lena@kestrellease.example ext 2</div></div>
    <div class="group"><div class="person"><b>Clara</b> – clara@kestrellease.example ext 5</div></div>
    <div class="group"><div class="person"><b>Ruby</b> – ruby@kestrellease.example ext 6</div></div>
    <div class="group"><div class="person"><b>Drew</b> – drew@kestrellease.example ext 3</div></div>
    <div class="legal">
      <div class="dept">Legal Department</div>
      <div class="dept-phone">800-555-0177</div>
      <div class="group first"><div class="person"><b>Joanna</b> – joanna@kestrellease.example ext 103</div></div>
    </div>
  </div>

  <address class="contact-address">
    <b>Kestrel Lease</b><br>
    P.O. Box 4410<br>
    Easley, SC 29640<br>
    Fax Number: 800-555-0199<br>
    Email: info@kestrellease.example
  </address>
</section>

<footer class="site-footer">
  <div class="footer-numbers">
    <span>Main Number: <b>800-555-0140</b></span><span class="sep">•</span>
    <span>Payment Center: <b>800-555-0177</b></span><span class="sep">•</span>
    <span>Fax Number: <b>800-555-0199</b></span><span class="sep">•</span>
    <span>Email: <b>info@kestrellease.example</b></span>
  </div>
  <div class="footer-address">P.O. Box 4410<br>Easley, SC 29640</div>
  <div class="footer-legal">Copyright © 2014 Kestrel Lease. All Rights Reserved<br>Privacy Policy | Terms and Conditions | Refunds</div>
</footer>

</body>
</html>
```